Business Card Design - Amberfield Court

We are looking at a new design for our business cards that has a modern and professional look. We run a residential aged care facility focussing on the care of residents. The cards will be used for potential clients, consultants and business opportunities in this sector. Blue and white is our main colours and would to see these colours incorporated in the design.
Industry/Entity Type
Business
Contact Information for Business Card
Amberfield Court, Darren Walsh, dwalsh@amberfieldcourt.com.au, Finance Manager, 0472 639 208, BCom, 37 Marrabel Crescent, Brindle Vale, Qld 4093.
Look and feel
Each slider illustrates characteristics of the customer's brand and the style your logo design should communicate.

```html
<!DOCTYPE html>
<html lang="en">
<head>
<meta charset="utf-8">
<title>Amberfield Court – Business Card</title>
<link rel="stylesheet" href="https://fonts.googleapis.com/css2?family=Arimo:ital,wght@0,400;0,700;1,400&display=swap">
<style>
  :root {
    --page-bg: #d9dbdd;
    --card-top: #f1f2f3;
    --card-bottom: #e2e4e6;
    --card-edge: #c7cacd;
    --navy: #2d5878;
    --band: #6f6760;
    --band-text: #e4e2df;
    --body-text: #3a4756;
  }
  * { box-sizing: border-box; margin: 0; padding: 0; }
  html, body {
    width: 1200px;
    height: 969px;
    overflow: hidden;
    background: var(--page-bg);
    font-family: "Arimo", Arial, sans-serif;
  }
  .card {
    position: absolute;
    left: 78px;
    top: 190px;
    width: 1045px;
    height: 589px;
    border-radius: 26px;
    background: linear-gradient(160deg, var(--card-top), var(--card-bottom));
    border: 1px solid var(--card-edge);
    box-shadow: 0 14px 40px rgba(40, 50, 60, 0.18);
  }
  .brand {
    position: absolute;
    right: 57px;
    top: 212px;
    display: flex;
    align-items: center;
    gap: 12px;
  }
  .brand-dot {
    width: 22px;
    height: 22px;
    border-radius: 50%;
    background: var(--navy);
  }
  .brand-name {
    font-weight: 700;
    font-size: 34px;
    letter-spacing: 1.5px;
    text-transform: uppercase;
    color: var(--navy);
  }
  .holder-name {
    position: absolute;
    left: 57px;
    top: 218px;
    font-weight: 700;
    font-size: 32px;
    color: var(--navy);
    text-transform: uppercase;
  }
  .holder-name .credential { font-size: 26px; }
  .title-band {
    position: absolute;
    left: 57px;
    top: 274px;
    width: 931px;
    height: 34px;
    background: var(--band);
    display: flex;
    align-items: center;
    justify-content: space-between;
    padding: 0 10px;
    color: var(--band-text);
  }
  .job-title { font-size: 26px; }
  .tagline { font-style: italic; font-size: 21px; }
  .contact-list {
    position: absolute;
    left: 57px;
    top: 430px;
    list-style: none;
    color: var(--body-text);
    font-size: 27px;
  }
  .contact-list li {
    display: flex;
    align-items: center;
    gap: 12px;
    height: 41px;
  }
  .contact-list svg { width: 24px; height: 24px; fill: var(--navy); flex: none; }
  .address {
    position: absolute;
    right: 57px;
    top: 471px;
    text-align: right;
    font-style: normal;
    color: var(--body-text);
    font-size: 27px;
    line-height: 41px;
  }
</style>
</head>
<body>
  <div class="card">
    <div class="brand">
      <span class="brand-dot"></span>
      <span class="brand-name">Amberfield Court</span>
    </div>

    <h1 class="holder-name">Darren Walsh <span class="credential">BCom</span></h1>

    <div class="title-band">
      <span class="job-title">Finance Manager</span>
      <span class="tagline">Caring, Comfort, Community</span>
    </div>

    <ul class="contact-list">
      <li>
        <svg viewBox="0 0 24 24" aria-hidden="true"><path d="M6.6 10.8a15.1 15.1 0 0 0 6.6 6.6l2.2-2.2c.3-.3.7-.4 1-.2 1.1.4 2.3.6 3.6.6.6 0 1 .4 1 1V20c0 .6-.4 1-1 1C10.6 21 3 13.4 3 4c0-.6.4-1 1-1h3.5c.6 0 1 .4 1 1 0 1.3.2 2.5.6 3.6.1.3 0 .7-.2 1z"/></svg>
        <span>0472 639 208</span>
      </li>
      <li>
        <svg viewBox="0 0 24 24" aria-hidden="true"><path d="M2 5h20v14H2z"/><path d="M3 6.5l9 6.5 9-6.5" fill="none" stroke="#e8eaec" stroke-width="1.6"/></svg>
        <span>dwalsh@amberfieldcourt.com.au</span>
      </li>
      <li>
        <svg viewBox="0 0 24 24" aria-hidden="true"><circle cx="12" cy="12" r="10"/><path d="M12 2c-3 3-3 17 0 20M12 2c3 3 3 17 0 20M2 12h20" fill="none" stroke="#e8eaec" stroke-width="1.4"/></svg>
        <span>www.amberfieldcourt.com.au</span>
      </li>
    </ul>

    <address class="address">
      37 Marrabel Crescent<br>
      Brindle Vale, Qld 4093.
    </address>
  </div>
</body>
</html>
```